Home Remodeling company needs a business card design

we need a business card design for home remodeling company in hamilton county, indiana USA. we offers a wide range of construction services including whole house renovations, Design and Build Basements and Kitchen and Bathroom Remodeling . we would like to see designs for both site of business card that use the same color of the company logo and also including all information below :
1- Karim Feltous CEO / General Contractor
2- all company contacts Telephone numbers ( 1-888-DULOM-47 ) ( 317-555-0193) email address ( info@dulomhome.com) website ( www.dulomhome.com ) and social media logos (Facebook- twitter- google plus )
3- company logo
4- licensed . insured . bonded

```html
<!DOCTYPE html>
<html lang="en">
<head>
<meta charset="utf-8">
<title>Dulom Home Remodeling – Business Card</title>
<link href="https://fonts.googleapis.com/css2?family=Arimo:wght@400&display=swap" rel="stylesheet">
<style>
  :root {
    --bg: #e9e6e1;
    --card: #ffffff;
    --ink: #3c3c3e;
    --grey: #6f7073;
    --tile: #8a8b8e;
    --band-grey: #5d5e60;
    --band-dark: #2f3031;
    --red: #d5343f;
    --text: #2a2a2a;
  }
  * { box-sizing: border-box; margin: 0; padding: 0; }
  html, body { width: 1200px; height: 892px; overflow: hidden; }
  body {
    background: var(--bg);
    display: flex; flex-direction: column; align-items: center; justify-content: center;
    gap: 40px;
    font-family: "Arimo", Arial, sans-serif;
  }
  .card {
    position: relative;
    width: 680px; height: 388px;
    background: var(--card);
    box-shadow: 0 6px 18px rgba(0,0,0,.15);
    overflow: hidden;
  }
  .card-bands { position: absolute; left: 0; bottom: 0; width: 100%; height: 86px; }

  .wordmark {
    position: absolute;
    font-family: "Arimo", Arial, sans-serif; font-weight: 400;
    color: var(--ink); line-height: 1.1; white-space: nowrap;
  }

  /* Logo side */
  .card--brand .wordmark { left: 60px; top: 110px; font-size: 46px; }
  .social { position: absolute; left: 214px; top: 214px; display: flex; gap: 18px; }
  .social-tile { width: 66px; height: 66px; background: var(--tile); }

  /* Contact side */
  .card--contact .wordmark { right: 44px; top: 54px; font-size: 36px; }
  .tagline {
    position: absolute; right: 44px; top: 122px;
    font-size: 22px; color: var(--text); letter-spacing: .5px;
  }
  .person { position: absolute; left: 44px; top: 202px; }
  .person-name { font-size: 26px; color: var(--red); }
  .person-title { font-size: 16px; color: var(--grey); margin-top: 6px; }
  .divider { position: absolute; left: 322px; top: 200px; width: 1px; height: 86px; background: #b9b9b9; }
  .contacts { position: absolute; left: 344px; top: 200px; list-style: none; }
  .contacts li { display: flex; align-items: center; gap: 10px; font-size: 17px; color: var(--text); height: 22px; }
  .contacts svg { width: 16px; height: 16px; flex: none; }
</style>
</head>
<body>

<section class="card card--brand" aria-label="Card front">
  <div class="wordmark">Dulom Home Remodeling</div>
  <div class="social" aria-label="Social media profiles">
    <span class="social-tile"></span><span class="social-tile"></span><span class="social-tile"></span>
  </div>
  <svg class="card-bands" viewBox="0 0 680 86" preserveAspectRatio="none" aria-hidden="true">
    <rect x="0" y="0" width="680" height="86" fill="var(--band-grey)"/>
    <rect x="0" y="34" width="680" height="4" fill="var(--band-dark)"/>
    <polygon points="300,38 330,30 680,30 680,86 286,86" fill="var(--red)"/>
  </svg>
</section>

<section class="card card--contact" aria-label="Card back">
  <div class="wordmark">Dulom Home Remodeling</div>
  <div class="tagline">licensed . insured . bonded</div>

  <div class="person">
    <div class="person-name">Karim Feltous</div>
    <div class="person-title">CEO / General Contractor</div>
  </div>
  <div class="divider"></div>
  <ul class="contacts">
    <li><svg viewBox="0 0 16 16"><rect width="16" height="16" fill="var(--red)"/><path d="M5 4h2l1 2.5-1.2.8a6 6 0 0 0 2 2l.8-1.2L12 9v2a1 1 0 0 1-1 1A7 7 0 0 1 4 5a1 1 0 0 1 1-1z" fill="#fff"/></svg>317-555-0193</li>
    <li><svg viewBox="0 0 16 16"><rect width="16" height="16" fill="var(--red)"/><path d="M5 4h2l1 2.5-1.2.8a6 6 0 0 0 2 2l.8-1.2L12 9v2a1 1 0 0 1-1 1A7 7 0 0 1 4 5a1 1 0 0 1 1-1z" fill="#fff"/></svg>1-888-DULOM-47</li>
    <li><svg viewBox="0 0 16 16"><rect width="16" height="16" fill="var(--red)"/><circle cx="8" cy="8" r="4.5" fill="none" stroke="#fff" stroke-width="1.2"/><path d="M3.5 8h9M8 3.5c-2 2.5-2 6.5 0 9M8 3.5c2 2.5 2 6.5 0 9" fill="none" stroke="#fff" stroke-width="1"/></svg>www.dulomhome.com</li>
    <li><svg viewBox="0 0 16 16"><rect width="16" height="16" fill="var(--red)"/><rect x="3" y="4.5" width="10" height="7" fill="none" stroke="#fff" stroke-width="1.2"/><path d="M3 4.5l5 4 5-4" fill="none" stroke="#fff" stroke-width="1.2"/></svg>info@dulomhome.com</li>
  </ul>

  <svg class="card-bands" viewBox="0 0 680 86" preserveAspectRatio="none" aria-hidden="true">
    <rect x="0" y="0" width="680" height="86" fill="var(--band-grey)"/>
    <rect x="0" y="34" width="680" height="4" fill="var(--band-dark)"/>
    <polygon points="300,38 330,30 680,30 680,86 286,86" fill="var(--red)"/>
  </svg>
</section>

</body>
</html>
```